LANTERN - and the quiet crafts of everyday life

I´m writing a book about CHANGE and the skills leaders needs to embody the transformation from being amanager to become leaders.
The title of the book in Icelandic is the same as the name of the project (which I want to be used on the designes is:) UPPSPRETTA
(with the subtitle:) og hugrekki hversdagsins

Change is not controlled or managed – Leading effective change is an art form which is one of the big reasons for why 70% of changes within companies fail. The main reason however, is that managers are tasked with managing and directing them. The art form of change is to put it in the hands of leaders who possess the emotional intelligence that is needed – all their other advantages intact – to lead change all the way.

The big problem when it comes to change is that there are too many managers and too few leaders within companies – leaders who possess emotional intelligence which is the most important skill a leader embodies to empower change. A leader has what it takes to empower followership.

A manager tends to push and control, make decisions that he presupposes others to implement the way he expects. An emotionally competent leader leads by example and enhances followership on that journey because of the trust and respect he has earned.

In few words: SOFT SKILLS ARE THE NEW HARD SKILLS!

```html
<!DOCTYPE html>
<html lang="is">
<head>
<meta charset="utf-8">
<title>UPPSPRETTA – og hugrekki hversdagsins</title>
<link rel="stylesheet" href="https://fonts.googleapis.com/css2?family=Libre+Franklin:wght@400;800&display=swap">
<style>
  :root {
    --coral-light: #e98a72;
    --coral: #e2684d;
    --coral-deep: #c9624e;
    --ink-white: #f1efee;
    --rule: rgba(255, 232, 224, 0.7);
    --glow: #fdeee8;
    --globe-dark: #8e2414;
    --globe-mid: #b8432d;
  }
  * { margin: 0; padding: 0; box-sizing: border-box; }
  html, body {
    width: 1200px;
    height: 1200px;
    overflow: hidden;
    background: #ffffff;
  }
  .book-cover {
    position: relative;
    width: 1200px;
    height: 1200px;
    overflow: hidden;
    background: linear-gradient(90deg, var(--coral-light) 0%, #dc7a62 18%, var(--coral-deep) 45%, #d8664e 72%, var(--coral) 92%, var(--coral-light) 100%);
  }
  .cover-spine-edge {
    position: absolute;
    top: 0;
    left: 0;
    width: 14px;
    height: 100%;
    background: linear-gradient(90deg, #f0a590 0%, #e2775d 100%);
  }
  .cover-spine-crease {
    position: absolute;
    top: 0;
    left: 14px;
    width: 42px;
    height: 100%;
    background: linear-gradient(90deg, #cf5f47 0%, #e98d76 35%, #e4795f 65%, rgba(226, 119, 94, 0) 100%);
  }
  .cover-right-edge {
    position: absolute;
    top: 0;
    right: 0;
    width: 22px;
    height: 100%;
    background: linear-gradient(90deg, rgba(233, 138, 114, 0) 0%, #f09a84 100%);
  }
  .cover-title {
    position: absolute;
    top: 78px;
    left: 0;
    width: 100%;
    text-align: center;
    font-family: "Libre Franklin", "Arial Black", sans-serif;
    font-weight: 800;
    font-size: 150px;
    line-height: 1;
    letter-spacing: -2px;
    color: var(--ink-white);
  }
  .cover-title span {
    display: inline-block;
    transform: scaleX(0.88);
    transform-origin: center;
  }
  .cover-subtitle-block {
    position: absolute;
    top: 261px;
    left: 259px;
    width: 672px;
    height: 87px;
    display: flex;
    align-items: center;
    justify-content: center;
  }
  .cover-subtitle-block::before,
  .cover-subtitle-block::after {
    content: "";
    position: absolute;
    left: 0;
    width: 100%;
    height: 1px;
    background: linear-gradient(90deg, rgba(255,232,224,0) 0%, var(--rule) 15%, var(--rule) 85%, rgba(255,232,224,0) 100%);
  }
  .cover-subtitle-block::before { top: 0; }
  .cover-subtitle-block::after { bottom: 0; }
  .cover-subtitle {
    font-family: "Libre Franklin", Arial, sans-serif;
    font-weight: 400;
    font-size: 53px;
    letter-spacing: 0.3px;
    color: var(--ink-white);
  }
  .cover-illustration {
    position: absolute;
    left: 238px;
    top: 402px;
    width: 775px;
    height: 775px;
    border-radius: 50%;
    background:
      radial-gradient(circle at 76% 40%, var(--glow) 0%, rgba(253, 238, 232, 0.75) 10%, rgba(240, 170, 150, 0.3) 30%, rgba(240, 170, 150, 0) 48%),
      radial-gradient(ellipse 55% 32% at 38% 22%, rgba(142, 36, 20, 0.95) 0%, rgba(142, 36, 20, 0.7) 55%, rgba(142, 36, 20, 0) 100%),
      radial-gradient(ellipse 30% 40% at 50% 78%, rgba(150, 40, 24, 0.55) 0%, rgba(150, 40, 24, 0) 100%),
      radial-gradient(circle at 50% 50%, #eaa08c 0%, #e0826a 60%, #d96c54 88%, rgba(217, 108, 84, 0) 100%);
  }
  .cover-floor {
    position: absolute;
    left: 200px;
    top: 1040px;
    width: 800px;
    height: 160px;
    background: linear-gradient(180deg, rgba(180, 60, 40, 0.35) 0%, rgba(210, 100, 78, 0.15) 60%, rgba(226, 104, 77, 0) 100%);
  }
</style>
</head>
<body>
  <main class="book-cover">
    <div class="cover-spine-edge"></div>
    <div class="cover-spine-crease"></div>
    <div class="cover-right-edge"></div>
    <h1 class="cover-title"><span>UPPSPRETTA</span></h1>
    <div class="cover-subtitle-block">
      <p class="cover-subtitle">og hugrekki hversdagsins</p>
    </div>
    <div class="cover-illustration" role="img" aria-label="Illustration: a glowing globe with connection lines, with silhouettes of business people talking and shaking hands in front of it"></div>
    <div class="cover-floor" role="img" aria-label="Reflections of the silhouetted figures on a glossy floor"></div>
  </main>
</body>
</html>
```